Kestal-Materials. Limestone; improving the world

New Limestone company and need logo design.
Limestone offsets carbon mitigation industries restore and replenish soil fertilities in the Prairies, the breadbasket of the world. At the same time, Limestone is proving a critical emergent component of carbon capture sequestration technology will therefore play a critical role in the development of the western Canadian energy industries
Our limestone resources are situated in the foothills of the Canadian Rockies well-positioned above the sprawling fields of the vast peace district.
Agriculture and oli sites
Kestal Materials
3 page

```html
<!DOCTYPE html>
<html lang="en">
<head>
<meta charset="utf-8">
<title>Kestal Materials</title>
<link href="https://fonts.googleapis.com/css2?family=Oswald:wght@500;600&family=Lato:wght@400;700&family=Arimo:wght@400;700&display=swap" rel="stylesheet">
<style>
:root{
  --ink:#111;
  --text:#333;
  --muted:#555;
  --blue:#3a8fc6;
  --green:#2e6b2f;
  --leaf:#4ea52a;
  --dark:#141414;
  --darker:#0b0b0b;
  --line:#dcdcdc;
  --white:#fff;
}
*{margin:0;padding:0;box-sizing:border-box}
html,body{width:1200px;height:4101px;overflow:hidden;background:var(--white)}
body{position:relative;font-family:'Lato',sans-serif;color:var(--text)}
.abs{position:absolute}
.heading{font-family:'Oswald',sans-serif;font-weight:600;color:var(--ink);font-size:42px;letter-spacing:.5px;line-height:1.1}
.center{left:0;width:1200px;text-align:center}
.body-copy{font-size:14.5px;line-height:28.4px;color:var(--text)}
.btn{display:flex;align-items:center;justify-content:center;background:var(--blue);color:var(--white);font-size:16px;font-weight:700;border-radius:26px;letter-spacing:.2px}
.chev{fill:none;stroke:#fff;stroke-width:2}

/* hero */
.hero{top:0;left:0;width:1200px;height:603px;background:
  linear-gradient(180deg,rgba(0,0,0,0) 0%,rgba(0,0,0,0) 62%,#9a6a42 74%,#7a4a2a 86%,#5e3519 100%),
  linear-gradient(90deg,#5f9e2a 0%,#8cc63c 35%,#a9d65a 60%,#c9e38a 85%,#e6f0c4 100%)}
.brand{font-weight:700;color:var(--white);font-size:21px;letter-spacing:.2px}
.nav{top:28px;left:436px;display:flex}
.nav a{color:var(--white);text-decoration:none;font-size:15.5px;margin-right:41px}
.nav a.active{text-decoration:underline}
.social{display:flex;gap:10px}
.social span{width:34px;height:34px;border-radius:50%;background:var(--leaf);border:2px solid #fff;display:block;box-shadow:inset 0 0 0 9px var(--leaf),inset 0 0 0 20px #6fbe45}
.hero-title{left:624px;top:202px;font-family:'Oswald',sans-serif;font-weight:500;color:var(--white);font-size:52px;letter-spacing:.5px;line-height:1.1}
.hero-copy{left:626px;top:272px;width:430px;color:var(--white);font-size:16px;line-height:27px}
.dots{left:562px;top:561px;display:flex;gap:10px}
.dots i{width:9px;height:9px;border-radius:50%;background:rgba(255,255,255,.45);display:block}
.dots i:first-child{background:#fff}

/* products */
.rock-band{top:891px;left:0;width:1200px;height:723px;background:linear-gradient(90deg,#eceef0 0%,#e6e8ea 38%,#c9c8c4 55%,#a9a7a1 72%,#bdbcb8 88%,#d4d3d0 100%)}
.card{top:815px;width:237px;height:299px;background:var(--white);border:1px solid var(--line);text-align:center}
.card svg{position:absolute;left:78px;top:24px}
.card h3{position:absolute;top:108px;left:0;width:100%;font-weight:400;font-size:20px;color:var(--ink)}
.card p{position:absolute;top:148px;left:14px;right:14px;font-size:12.5px;line-height:25px;color:var(--muted)}
.card .bar{position:absolute;bottom:0;left:52px;width:133px;height:3px;background:var(--blue)}

/* media */
.photo{background:linear-gradient(180deg,#c4c8cb 0%,#a7a9a6 45%,#8f877a 70%,#7d6e58 100%)}
.play{width:60px;height:60px;border-radius:50%;background:#1b1b1b;border:3px solid #3c8a2f;display:flex;align-items:center;justify-content:center}
.sustain{background:linear-gradient(180deg,#f6dccb 0%,#f1cdb5 80%,#d99274 81%,#e3a586 100%)}
.lime-band{top:2519px;left:0;width:1200px;height:381px;background:
  linear-gradient(180deg,rgba(0,0,0,0) 70%,#3e6a1a 85%,#2c4a12 100%),
  linear-gradient(90deg,#3f6d1e 0%,#6c9a2e 25%,#a8b84a 50%,#6c9a2e 75%,#3f6d1e 100%)}

/* news */
.news{top:3107px;width:314px;height:415px;border:1px solid var(--line);background:var(--white)}
.news .img{height:218px}
.news h4{position:absolute;top:240px;left:13px;right:13px;font-family:'Arimo',sans-serif;font-weight:700;font-size:17px;line-height:25px;color:var(--ink)}
.news p{position:absolute;top:298px;left:13px;right:13px;font-size:12px;line-height:25.5px;color:var(--muted)}
.news a{position:absolute;top:380px;left:13px;color:var(--blue);font-size:16px;text-decoration:underline}

/* contact strip + footer */
.strip{top:3606px;left:0;width:1200px;height:123px;background:var(--dark)}
.strip .divider{position:absolute;top:0;width:1px;height:123px;background:#333}
.info{position:absolute;display:flex;align-items:center;gap:16px;color:var(--white);font-size:14.5px;line-height:22px}
.info b{font-weight:700}
.ring{width:58px;height:58px;border-radius:50%;border:2px solid #fff;display:flex;align-items:center;justify-content:center;flex:none}
.footer{top:3729px;left:0;width:1200px;height:313px;background:var(--darker);color:var(--white)}
.footer-title{position:absolute;color:var(--white);font-size:18px;font-weight:700}
.field{position:absolute;background:var(--white);border-radius:4px;color:#666;font-size:15px;padding:16px 18px}
.links{position:absolute;left:985px;top:3806px;list-style:none;color:var(--white);font-size:15px;line-height:25.6px}
.ring-sm{width:30px;height:30px;border-radius:50%;border:1.5px solid #fff;background:#2a2a2a;display:block}
.bottom{top:4042px;left:0;width:1200px;height:59px;background:var(--darker);border-top:1px solid #222;color:var(--white);font-size:14.5px;text-align:center;line-height:59px}
</style>
</head>
<body>

<!-- Hero -->
<section class="abs hero" role="img" aria-label="Light bulb with a young tree growing inside, set on soil against a green background, ringed by eco icons"></section>
<div class="abs brand" style="left:110px;top:26px">KESTAL MATERIALS</div>
<nav class="abs nav">
  <a class="active">HOME</a><a>ABOUT US</a><a>SERVICES</a><a>NEWS</a><a>CONTACT US</a>
</nav>
<div class="abs social" style="left:960px;top:22px"><span></span><span></span><span></span></div>
<svg class="abs" style="left:73px;top:281px" width="22" height="42"><path class="chev" d="M20 1 L2 21 L20 41"/></svg>
<svg class="abs" style="left:1107px;top:281px" width="22" height="42"><path class="chev" d="M2 1 L20 21 L2 41"/></svg>
<h1 class="abs hero-title">KESTAL MATERIALS</h1>
<p class="abs hero-copy">Lorem ipsum dolor sit amet, consectetur adipiscing elit, sed do eiusmod tempor incididunt ut labore et dolore magna aliqua. Ut enim ad minim veniam,</p>
<div class="abs btn" style="left:625px;top:376px;width:183px;height:48px">GET STARTED</div>
<div class="abs dots"><i></i><i></i><i></i><i></i></div>

<!-- Products -->
<div class="abs rock-band" role="img" aria-label="Pale limestone quarry rock face with broken stone"></div>
<h2 class="abs heading center" style="top:678px">OUR PRODUCTS</h2>
<p class="abs center body-copy" style="top:736px;font-size:15.5px;line-height:26px">Lorem ipsum dolor sit amet, consectetur adipiscing elit, sed do eiusmod tempor incididunt ut<br>labore et dolore magna aliqua. Ut enim ad minim veniam, quis nostrud</p>
<svg class="abs" style="left:70px;top:954px" width="14" height="26"><path d="M12 1 L2 13 L12 25" fill="none" stroke="#333" stroke-width="1.5"/></svg>
<svg class="abs" style="left:1116px;top:954px" width="14" height="26"><path d="M2 1 L12 13 L2 25" fill="none" stroke="#333" stroke-width="1.5"/></svg>

<div class="abs card" style="left:97px">
  <svg width="80" height="64" viewBox="0 0 80 64" fill="none" stroke="#2e6b2f" stroke-width="2.5"><circle cx="48" cy="32" r="24"/><circle cx="48" cy="32" r="18"/><path d="M48 20 V32 H58"/><path d="M6 18 H22 M2 30 H20 M8 42 H22"/></svg>
  <h3>Quicklime</h3>
  <p>Sed ut pspiciatis unde omnis isttus error em accusantium doloremque laudantium, totem aperiam, eaque ipsa quae ab il inventore veritatis et quasi architecto</p>
  <div class="bar"></div>
</div>
<div class="abs card" style="left:353px">
  <svg width="80" height="64" viewBox="0 0 80 64" fill="none" stroke="#2e6b2f" stroke-width="2.5"><path d="M40 2 C34 12 32 16 32 20 A8 8 0 0 0 48 20 C48 16 46 12 40 2Z"/><path d="M18 32 H62 V46 H18Z M14 52 H66 M18 58 H62"/><path d="M24 38 Q32 34 40 38 T56 38"/></svg>
  <h3>Hydrated Lime</h3>
  <p>Sed ut pspiciatis unde omnis isttus error em accusantium doloremque laudantium, totem aperiam, eaque ipsa quae ab il inventore veritatis et quasi architecto</p>
  <div class="bar"></div>
</div>
<div class="abs card" style="left:608px">
  <svg width="80" height="64" viewBox="0 0 80 64" fill="none" stroke="#2e6b2f" stroke-width="2.5"><path d="M6 60 H74 M10 60 V34 H28 V60 M52 60 V34 H70 V60 M30 60 V12 H50 V60 M36 12 V4 H44 V12 M36 22 V50 M44 22 V50"/></svg>
  <h3>Pulverized Limestone</h3>
  <p>Sed ut pspiciatis unde omnis isttus error em accusantium doloremque laudantium, totem aperiam, eaque ipsa quae ab il inventore veritatis et quasi architecto</p>
  <div class="bar"></div>
</div>
<div class="abs card" style="left:864px">
  <svg width="80" height="64" viewBox="0 0 80 64" fill="none" stroke="#2e6b2f" stroke-width="2.5"><path d="M8 52 L16 28 L34 16 L56 20 L70 36 L72 52 Z"/><path d="M4 58 H76 M30 30 L42 40 M48 28 L56 40"/></svg>
  <h3>Construction Stone</h3>
  <p>Sed ut pspiciatis unde omnis isttus error em accusantium doloremque laudantium, totem aperiam, eaque ipsa quae ab il inventore veritatis et quasi architecto</p>
  <div class="bar"></div>
</div>

<!-- Who we are -->
<h2 class="abs heading" style="left:111px;top:1190px">WHO WE ARE</h2>
<p class="abs body-copy" style="left:111px;top:1256px;width:450px">Lorem ipsum dolor sit sectetur adipiing eit, sed do eiusmod tempor incididunt ut laagna aliqua. Ut enim ad minim veniam, quis nostrud exercitation ullamco laboris nisi utuip ex ea commodo consequat. Duis auteLem ipsum dolor sit amet, consectetur adipiscing elit, sed do eiusmod tempor incididunt ut labore et dolore magna aliqua. Ut enim ad minim veniam, quis nostrud exercitation ullamco laboris nisi ut aliquip .</p>
<div class="abs btn" style="left:111px;top:1477px;width:182px;height:51px">LEARN MORE</div>

<!-- Mission -->
<div class="abs photo" style="left:111px;top:1695px;width:471px;height:328px" role="img" aria-label="Stone crushing conveyor plant at a quarry with gravel piles and dust"></div>
<div class="abs play" style="left:317px;top:1829px"><svg width="16" height="18"><path d="M2 1 L15 9 L2 17Z" fill="#fff"/></svg></div>
<h2 class="abs heading" style="left:643px;top:1689px">OUR MISSION</h2>
<p class="abs body-copy" style="left:643px;top:1754px;width:450px">Lorem ipsum dolor sit sectetur adipiing eit, sed do eiusmod tempor incididunt ut laagna aliqua. Ut enim ad minim veniam, quis nostrud exercitation ullamco laboris nisi utuip ex ea commodo consequat. Duis auteLem ipsum dolor sit amet, consectetur adipiscing elit, sed do eiusmod tempor incididunt ut labore et dolore magna aliqua. Ut enim ad minim veniam, quis nostrud exercitation ullamco laboris nisi ut aliquip .</p>
<div class="abs btn" style="left:643px;top:1977px;width:182px;height:50px">LEARN MORE</div>

<!-- Sustainability -->
<h2 class="abs heading" style="left:111px;top:2100px">SUSTAINABILITY</h2>
<p class="abs body-copy" style="left:111px;top:2165px;width:450px">Lorem ipsum dolor sit sectetur adipiing eit, sed do eiusmod tempor incididunt ut laagna aliqua. Ut enim ad minim veniam, quis nostrud exercitation ullamco laboris nisi utuip ex ea commodo consequat. Duis auteLem ipsum dolor sit amet, consectetur adipiscing elit, sed do eiusmod tempor incididunt ut labore et dolore magna aliqua. Ut enim ad minim veniam, quis nostrud exercitation ullamco laboris nisi ut aliquip .</p>
<div class="abs btn" style="left:111px;top:2387px;width:183px;height:50px">LEARN MORE</div>
<div class="abs sustain" style="left:617px;top:2106px;width:472px;height:329px" role="img" aria-label="Hand-drawn sustainability doodles of a car, sun, bulb, bicycle and recycling signs on a peach wall"></div>

<!-- What is lime -->
<section class="abs lime-band" role="img" aria-label="Fern leaves and moss in soft green forest light"></section>
<h2 class="abs heading center" style="top:2592px;color:#fff;font-size:40px">WHAT IS LIME?</h2>
<p class="abs center" style="top:2662px;color:#fff;font-size:15.5px;line-height:27px">Lorem ipsum dolor sit amet, consectetur adipiscing elit, sed do eiusmod tempor incididunt ut labore et dolore magna<br>aliqua. Ut enim ad minim veniam, quis nostrud exercitation ullamco laboris nisi ut aliquip ex ea commodo consequat.<br>Duis aute irure dolor in reprehenderit in voluptate velit esse cillum dolore eu fugiat nulla pariatur.</p>
<div class="abs btn" style="left:509px;top:2763px;width:182px;height:49px">LEARN MORE</div>

<!-- Latest news -->
<h2 class="abs heading center" style="top:2975px">LATEST NEWS</h2>
<p class="abs center body-copy" style="top:3033px;font-size:15.5px;line-height:26px">Lorem ipsum dolor sit amet, consectetur adipiscing elit, sed do eiusmod tempor incididunt ut<br>labore et dolore magna aliqua. Ut enim ad minim veniam, quis nostrud</p>

<article class="abs news" style="left:111px">
  <div class="img" style="background:linear-gradient(180deg,#7f8f5c 0%,#b9b4a2 40%,#cfcab8 60%,#6d8a5a 100%)" role="img" aria-label="Aerial view of a terraced open-pit quarry with a green pool"></div>
  <h4>Lorem ipsum dolor si consectetur adipiscing elit, sed do</h4>
  <p>Lorem ipsum dolor sit amet, consectet adipiscing elit, sed do eiusmod tempor incididnt ut labore et dolore magna aliqua.</p>
  <a>LEARN MORE &raquo;</a>
</article>
<article class="abs news" style="left:442px">
  <div class="img" style="background:linear-gradient(180deg,#7a6a4c 0%,#6b6a40 45%,#8e938c 70%,#4f5a3a 100%)" role="img" aria-label="Limestone cliff face above a stream with green vegetation"></div>
  <h4>Lorem ipsum dolor si consectetur adipiscing elit, sed do</h4>
  <p>Lorem ipsum dolor sit amet, consectet adipiscing elit, sed do eiusmod tempor incididnt ut labore et dolore magna aliqua.</p>
  <a>LEARN MORE &raquo;</a>
</article>
<article class="abs news" style="left:773px">
  <div class="img" style="background:linear-gradient(180deg,#a3a3a3 0%,#d2d2d2 45%,#9a9a9a 75%,#3a3a3a 100%)" role="img" aria-label="Industrial smokestacks releasing grey smoke"></div>
  <h4>Lorem ipsum dolor si consectetur adipiscing elit, sed do</h4>
  <p>Lorem ipsum dolor sit amet, consectet adipiscing elit, sed do eiusmod tempor incididnt ut labore et dolore magna aliqua.</p>
  <a>LEARN MORE &raquo;</a>
</article>

<!-- Contact strip -->
<section class="abs strip">
  <div class="divider" style="left:442px"></div>
  <div class="divider" style="left:761px"></div>
  <div class="info" style="left:138px;top:30px">
    <div class="ring"><svg width="22" height="30" viewBox="0 0 22 30"><path d="M11 1 A10 10 0 0 0 1 11 C1 19 11 29 11 29 C11 29 21 19 21 11 A10 10 0 0 0 11 1Z" fill="#fff"/><circle cx="11" cy="11" r="4" fill="#141414"/></svg></div>
    <div><b>Address:</b><br>123 Avenue name, City name<br>10150, United States</div>
  </div>
  <div class="info" style="left:513px;top:32px">
    <div class="ring"><svg width="26" height="26" viewBox="0 0 24 24"><path d="M5 2 L9 2 L10 7 L7.5 8.5 C8.5 11 12.5 15 15.5 16.5 L17 14 L22 15 L22 19 C22 21 20 22 18 22 C9 21 3 15 2 6 C2 4 3 2 5 2Z" fill="none" stroke="#fff" stroke-width="1.6"/></svg></div>
    <div><b>Phone:</b><br>(888) 888-8888</div>
  </div>
  <div class="info" style="left:788px;top:32px">
    <div class="ring"><svg width="26" height="20" viewBox="0 0 26 20"><rect x="1" y="1" width="24" height="18" fill="#fff"/><path d="M1 1 L13 11 L25 1 M1 19 L10 9 M25 19 L16 9" fill="none" stroke="#141414" stroke-width="1.6"/></svg></div>
    <div><b>Email</b><br>info@KestalMaterials.com</div>
  </div>
</section>

<!-- Footer -->
<footer class="abs footer"></footer>
<div class="abs brand" style="left:108px;top:3777px;font-size:23px">KESTAL MATERIALS</div>
<p class="abs" style="left:109px;top:3818px;width:310px;color:#fff;font-size:14.5px;line-height:26px">commodo consequat. Duis aute irure dolor in reprehenderit in voluptate velit esse cillum dolore eu fugiat nulla pariatur. Excepteur sint occaecat cupidatat non proident, sunt in culpa qui officia deserunt mollit an</p>
<div class="abs" style="left:115px;top:3964px;display:flex;gap:10px"><span class="ring-sm"></span><span class="ring-sm"></span><span class="ring-sm"></span><span class="ring-sm"></span></div>

<div class="footer-title" style="left:457px;top:3768px">CONTACT US</div>
<div class="field" style="left:457px;top:3807px;width:223px;height:51px">Name</div>
<div class="field" style="left:688px;top:3807px;width:224px;height:51px">Email</div>
<div class="field" style="left:457px;top:3869px;width:455px;height:78px">Message</div>
<div class="abs btn" style="left:457px;top:3963px;width:157px;height:49px;font-weight:400;font-size:16.5px">SUBSCRIBE</div>

<div class="footer-title" style="left:985px;top:3768px">QUICK LINK</div>
<ul class="links"><li>Home</li><li>About Us</li><li>Services</li><li>News</li><li>Contact Us</li></ul>

<div class="abs bottom">Kestal Materials &copy; 2021All Rights Reserved | Privacy Policy</div>

</body>
</html>
```